Design a building access mobile app for Quillo by Tamberlin Entry Systems

Hello, We're looking for an awesome designer to create an app design for our app Quillo, by Tamberlin Entry Systems. the mobile app allows employees open their office doors with their mobile phone. this means they don't have to use those plastic card badges or keys. We like clean modern design, dark and light themes. We don't have a logo yet.
Updates

Reason: Waiting on a couple designers to submit concepts

Target Market(s)

Commercial and employees

Industry/Entity Type

Building

Font styles to use
Sans Serif
Other font styles liked:
• Oswald extra light

Requirements
Must have
• nice clean design

```html
<!DOCTYPE html>
<html lang="en">
<head>
<meta charset="utf-8">
<title>Quillo – Sign Up</title>
<link rel="stylesheet" href="https://fonts.googleapis.com/css2?family=Montserrat:wght@400;500;600;700&display=swap">
<style>
  :root {
    --board-bg: #e3e7ef;
    --header-bg: #ffffff;
    --header-ink: #111111;
    --screen-bg: #0f0f0f;
    --field-bg: #252525;
    --accent: #1aa3f5;
    --ink-light: #ffffff;
    --ink-muted: #6a6a6a;
    --icon-stroke: #9a9a9a;
  }
  * { box-sizing: border-box; margin: 0; padding: 0; }
  html, body {
    width: 800px; height: 1200px; overflow: hidden;
    background: var(--board-bg);
    font-family: "Montserrat", sans-serif;
  }
  .board-header {
    position: absolute; left: 0; top: 0; width: 800px; height: 64px;
    background: var(--header-bg);
    display: flex; align-items: center; justify-content: space-between;
    padding: 0 18px;
  }
  .board-title { font-size: 25px; font-weight: 500; color: var(--header-ink); letter-spacing: 0.3px; }
  .board-meta { font-size: 18px; font-weight: 500; color: var(--header-ink); }

  .screen {
    position: absolute; left: 100px; top: 92px; width: 600px; height: 1067px;
    background: var(--screen-bg); overflow: hidden;
    box-shadow: 0 4px 14px rgba(0,0,0,0.18);
  }
  .hero-photo {
    position: absolute; left: 0; top: 0; width: 600px; height: 760px;
    background:
      radial-gradient(ellipse at 30% 25%, rgba(70,62,60,0.55), transparent 55%),
      radial-gradient(ellipse at 80% 45%, rgba(55,50,50,0.5), transparent 60%),
      linear-gradient(180deg, #2b2828 0%, #1f1d1d 45%, #0f0f0f 100%);
  }
  .back-button { position: absolute; left: 24px; top: 50px; width: 22px; height: 36px; }
  .screen-title {
    position: absolute; left: 0; width: 100%; top: 266px;
    text-align: center; font-size: 31px; font-weight: 700; color: var(--accent); letter-spacing: 0.5px;
  }
  .field {
    position: absolute; left: 40px; width: 520px; height: 88px; border-radius: 44px;
    background: var(--field-bg);
    display: flex; align-items: center;
  }
  .field-email { top: 504px; }
  .field-password { top: 616px; }
  .field-icon { position: absolute; left: 36px; width: 32px; height: 32px; }
  .field-label { position: absolute; left: 97px; font-size: 24px; font-weight: 500; color: var(--ink-light); }

  .fingerprint-toggle {
    position: absolute; top: 750px; left: 0; width: 100%;
    display: flex; align-items: center; justify-content: center; gap: 14px;
  }
  .fingerprint-icon { width: 46px; height: 46px; }
  .fingerprint-label { font-size: 24px; font-weight: 500; color: var(--accent); }

  .register-button {
    position: absolute; left: 40px; top: 846px; width: 520px; height: 86px;
    border: 2px solid var(--ink-light); border-radius: 43px;
    display: flex; align-items: center; justify-content: center;
    font-size: 23px; font-weight: 700; color: var(--ink-light); letter-spacing: 0.3px;
    background: transparent;
  }
  .terms-link {
    position: absolute; left: 0; width: 100%; top: 978px;
    text-align: center; font-size: 24px; font-weight: 500; color: var(--ink-muted);
  }
</style>
</head>
<body>
  <header class="board-header">
    <span class="board-title">Harrowgate Security</span>
    <span class="board-meta">Version 1 / 7 Screens</span>
  </header>

  <main class="screen">
    <div class="hero-photo" role="img" aria-label="Dimmed photo of hands holding a smartphone"></div>

    <svg class="back-button" viewBox="0 0 22 36" aria-label="Back">
      <polyline points="20,2 3,18 20,34" fill="none" stroke="#ffffff" stroke-width="2"/>
    </svg>

    <h1 class="screen-title">SIGN UP</h1>

    <div class="field field-email">
      <svg class="field-icon" viewBox="0 0 32 32" aria-hidden="true">
        <rect x="1" y="4" width="30" height="24" fill="none" stroke="var(--icon-stroke)" stroke-width="1.6"/>
        <polyline points="1,4 16,19 31,4" fill="none" stroke="var(--icon-stroke)" stroke-width="1.6"/>
      </svg>
      <span class="field-label">Email</span>
    </div>

    <div class="field field-password">
      <svg class="field-icon" viewBox="0 0 32 40" style="height:40px" aria-hidden="true">
        <path d="M9 14 V9 a7 7 0 0 1 14 0 V14" fill="none" stroke="var(--icon-stroke)" stroke-width="1.6"/>
        <circle cx="16" cy="24" r="15" fill="none" stroke="var(--icon-stroke)" stroke-width="1.6"/>
        <circle cx="16" cy="24" r="3" fill="none" stroke="var(--icon-stroke)" stroke-width="1.6"/>
      </svg>
      <span class="field-label">Password</span>
    </div>

    <div class="fingerprint-toggle">
      <svg class="fingerprint-icon" viewBox="0 0 46 46" aria-hidden="true">
        <g fill="none" stroke="var(--accent)" stroke-width="1.4" stroke-linecap="round">
          <path d="M6 30 C3 18 10 5 22 5 C33 5 40 14 38 26"/>
          <path d="M10 34 C7 22 12 10 22 10 C31 10 35 18 33 28"/>
          <path d="M14 37 C12 26 15 15 22 15 C28 15 30 21 29 30"/>
          <path d="M18 39 C17 30 18 20 22 20 C25 20 26 25 25 33"/>
          <path d="M22 25 C22 31 22 35 21 40"/>
        </g>
        <circle cx="36" cy="36" r="9" fill="var(--accent)" stroke="var(--screen-bg)" stroke-width="2"/>
        <polyline points="31.5,36 35,39.5 41,33" fill="none" stroke="#ffffff" stroke-width="2"/>
      </svg>
      <span class="fingerprint-label">Enable Fingerprint</span>
    </div>

    <div class="register-button">Register</div>

    <div class="terms-link">Terms &amp; Conditions</div>
  </main>
</body>
</html>
```